Communication and Marketing agency needs a new presentation card

We are a group of communication and marketing agencies specialized in companies that are in the logistics and industrial sector. The head agency is TELVANO Grupo and the group consists of 4 agencies: TELVANO Media, TELVANO Digital, TELVANO Research and DifundeEnPantalla. We hace 4 offices in Spain (Madrid, Barcelona, Valencia and Murcia). We are looking for a clean and attractive design that transmits our experience, brand presence in the market and knowledge to those who receive the card.It has to maintain the colors of the logo that is attached.
Target Market(s)
logistics and industrial sector
Marketing department
Contact Information for Business Card
Clean and attractive design

```html
<!DOCTYPE html>
<html lang="es">
<head>
<meta charset="utf-8">
<title>TELVANO Grupo – Business Card</title>
<link rel="stylesheet" href="https://fonts.googleapis.com/css2?family=Arimo:wght@400;700&family=Cinzel:wght@500;600&display=swap">
<style>
  :root {
    --backdrop: #8c5330;
    --kraft-light: #d4ad80;
    --kraft-mid: #c59866;
    --kraft-dark: #b88855;
    --ink: #111111;
    --rule: #3a2a1a;
  }
  * { margin: 0; padding: 0; box-sizing: border-box; }
  html, body {
    width: 1200px; height: 900px; overflow: hidden;
    background: var(--backdrop);
  }
  .canvas { position: relative; width: 1200px; height: 900px; }
  .card {
    position: absolute;
    background: linear-gradient(135deg, var(--kraft-light) 0%, var(--kraft-mid) 50%, var(--kraft-dark) 100%);
    color: var(--ink);
    font-family: "Arimo", Arial, sans-serif;
    box-shadow: 3px 4px 6px rgba(0,0,0,0.35);
  }
  .card--front { left: 330px; top: 90px; width: 555px; height: 343px; text-align: center; }
  .card--back  { left: 330px; top: 469px; width: 559px; height: 343px; }

  .contact-name {
    margin-top: 62px;
    font-family: "Cinzel", "Times New Roman", serif;
    font-weight: 600; font-size: 23px; letter-spacing: 0.5px; line-height: 1;
  }
  .contact-role { font-size: 16px; margin-top: 2px; line-height: 20px; }
  .divider { width: 195px; height: 1px; background: var(--ink); margin: 10px auto 0; }
  .contact-lines { margin-top: 10px; font-size: 16px; line-height: 20.5px; }
  .contact-lines b { font-weight: 700; }
  .divider--lower { margin-top: 10px; }
  .address { margin-top: 15px; font-size: 16px; line-height: 20px; }

  .group-mark {
    position: absolute; left: 143px; top: 124px; width: 280px;
    font-weight: 400; line-height: 1;
  }
  .group-mark__name { display: block; font-size: 56px; letter-spacing: 3px; }
  .group-mark__sub { display: block; font-size: 28px; text-align: right; margin-top: 6px; padding-right: 8px; }

  .agency-rule { position: absolute; left: 52px; top: 256px; width: 455px; height: 1px; background: var(--rule); }
  .agencies {
    position: absolute; left: 44px; top: 272px; width: 476px;
    display: flex; justify-content: space-between;
  }
  .agency { font-weight: 400; line-height: 1; }
  .agency__name { display: block; font-size: 18px; letter-spacing: 2.5px; }
  .agency__sub { display: block; font-size: 12px; text-align: right; margin-top: 3px; padding-right: 3px; }
  .agency--stacked .agency__name { font-size: 15px; letter-spacing: 0.5px; line-height: 16px; }
</style>
</head>
<body>
<main class="canvas">
  <section class="card card--front">
    <h1 class="contact-name">LUCAS BERRANDEZ</h1>
    <p class="contact-role">Managing Director</p>
    <div class="divider"></div>
    <p class="contact-lines">
      <b>P:</b> 034-910 552 381<br>
      <b>M:</b> 034-910 552 381<br>
      <b>E:</b> hola@telvanogrupo.es<br>
      <b>W:</b> www.telvanogrupo.es
    </p>
    <div class="divider divider--lower"></div>
    <p class="address">48, Calle Alcalá Norte<br>Madrid, 28014.</p>
  </section>

  <section class="card card--back">
    <div class="group-mark">
      <span class="group-mark__name">TELVANO</span>
      <span class="group-mark__sub">Grupo</span>
    </div>
    <div class="agency-rule"></div>
    <div class="agencies">
      <div class="agency"><span class="agency__name">TELVANO</span><span class="agency__sub">Research</span></div>
      <div class="agency"><span class="agency__name">TELVANO</span><span class="agency__sub">Digital</span></div>
      <div class="agency"><span class="agency__name">TELVANO</span><span class="agency__sub">Media</span></div>
      <div class="agency agency--stacked"><span class="agency__name">DIFUNDE</span><span class="agency__name">ENPANTALLA</span></div>
    </div>
  </section>
</main>
</body>
</html>
```